Etiketten für Bio Seifen
Zielgruppe
Wir stellen hochwertig 'handgemachte' Bio-Seifen her. Die Zielgruppe ist von 3-99 Jahren und zusätzlich haben wir auch noch Seife für Hunde.
Der Firmenname ist 'Verdolina'
Aufgabenstellung
Das Etikett soll Bezug auf Natur, Bio, Nachhaltigkeit nehmen. Wir stellen uns 'weiche' Aquarellfarben vor...Seife: Lavendel, Calendular, 7 Kräuter etc.
Das Etikett soll auf eine Beutelschachtel. Die Schachtel hat eine Anmaße: Breite 55mm; Höhe 120mm; Tiefe 30mm
Das Etikett soll im vorderen- und hinteren Bereich zusammenhängend geklebt werden.
Das Etikett soll eine Abmaße von: Breite 51mm; Höhe 114mm haben (Vorderseite) Rückseite gleich.
Wir möchten die Produkte auch gerne nummerieren, d.h. jede Seife hat eine Nummer die nicht zu groß dargestellt werden soll aber trotzdem gut leserlich.
Wir haben noch ein paar Bilder hochgeladen wie wir uns das ungefähr vorstellen.

```html
<!DOCTYPE html>
<html lang="de">
<head>
<meta charset="utf-8">
<title>Verdolina Bio Seife Etiketten</title>
<link href="https://fonts.googleapis.com/css2?family=Josefin+Sans:wght@300;400&family=Raleway:wght@300;400&family=Great+Vibes&display=swap" rel="stylesheet">
<style>
  :root {
    --paper: #ffffff;
    --ink: #111111;
    --violet: #4b2a8c;
    --rule: #5a3a93;
    --lilac: #b99ad0;
    --pink: #e7bfdc;
    --mist: #f3e8f3;
    --lavender: #a999d6;
  }
  * { margin: 0; padding: 0; box-sizing: border-box; }
  html, body { width: 1200px; height: 849px; overflow: hidden; background: var(--paper); }
  .sheet { position: relative; width: 1200px; height: 849px; background: var(--paper); }

  .sheet-title {
    position: absolute; left: 79px; top: 61px;
    font-family: "Raleway", sans-serif; font-weight: 400; font-size: 15px;
    color: var(--ink);
  }
  .rule { position: absolute; left: 0; width: 1200px; height: 1.2px; background: var(--rule); }
  .rule--top { top: 85px; }
  .rule--bottom { top: 793px; }

  .label {
    position: absolute; left: 77px; top: 166px; width: 206px; height: 460px;
    overflow: hidden;
  }
  .label-wash {
    position: absolute; inset: 0;
    background:
      radial-gradient(ellipse at 15% 75%, rgba(169,153,214,.85), transparent 45%),
      radial-gradient(ellipse at 85% 20%, rgba(231,191,220,.7), transparent 50%),
      linear-gradient(180deg, #cfa9d9 0%, #e2c6e6 30%, #dcc3e8 55%, #e6bfdf 80%, #efcde6 100%);
  }
  .label-band {
    position: absolute; left: 0; top: 123px; width: 100%; height: 150px;
    background: rgba(246, 236, 246, .72);
  }
  .label-text { position: absolute; left: 0; width: 100%; text-align: center; }
  .brand {
    top: 158px; font-family: "Josefin Sans", sans-serif; font-weight: 300;
    font-size: 20px; letter-spacing: 1.5px; color: #2a2330;
  }
  .category {
    top: 181px; font-family: "Raleway", sans-serif; font-size: 8px;
    letter-spacing: .8px; color: #2a2330;
  }
  .handmade {
    top: 190px; font-family: "Great Vibes", cursive; font-size: 11px;
    color: #6c5f75;
  }
  .variety {
    top: 205px; font-family: "Josefin Sans", sans-serif; font-weight: 400;
    font-size: 24px; letter-spacing: .5px; color: var(--violet);
  }
  .number {
    top: 232px; font-family: "Josefin Sans", sans-serif; font-size: 9px;
    letter-spacing: .6px; color: #2a2330;
  }

  .swatch {
    position: absolute; left: 390px; width: 69px; height: 69px;
    border-radius: 50%; border: 1.5px solid var(--violet);
  }
  .swatch--wash { top: 308px; background: linear-gradient(120deg, #f1e1ef, #e8c9e3 60%, #f0dcee); }
  .swatch--pattern { top: 390px; background: #ebd3ea; }
</style>
</head>
<body>
<main class="sheet">
  <h1 class="sheet-title">Verdolina Bio Seife Etiketten - Entwurfshafen - Januar 2022</h1>
  <div class="rule rule--top"></div>

  <section class="label" aria-label="Etikett Vorderseite">
    <div class="label-wash" role="img" aria-label="Aquarellfläche in Lavendel und Rosa mit feinem geometrischem Linienmuster"></div>
    <div class="label-band"></div>
    <p class="label-text brand">VERDOLINA</p>
    <p class="label-text category">BIO SEIFE</p>
    <p class="label-text handmade">Handgemachte</p>
    <p class="label-text variety">LAVENDEL</p>
    <p class="label-text number">NR. 1</p>
  </section>

  <div class="swatch swatch--wash" role="img" aria-label="Farbmuster Aquarell Rosa"></div>
  <div class="swatch swatch--pattern" role="img" aria-label="Farbmuster mit geometrischem Linienmotiv"></div>

  <div class="rule rule--bottom"></div>
</main>
</body>
</html>
```